Larkspur Talent IT Recruiting firm needs a business card design for Recruiters, Sourcers, and Account

We need business cards that allow us to change all contact info, names, titles (Recruiter, Sourcer, Account Manager, Director, CEO, etc) per person since we have three offices, in three cities, Phoenix, Austin, and Las Vegas. We do recruiting and contractors for IT positions (Developers, Architects, Software Engineers, Security Engineers, Help Desk, DBAs, PMs, Scrum Masters, etc.) Our client companies are very diverse from Meridian 100 to silicone Valley type start-ups.

So, while we what hip, techie, and quirky, it still needs to be professional. Primary color we use is blue, with silver as a secondary color.

Target Market(s)

IT, Technology

Industry/Entity Type

Business

Contact Information for Business Card

Company name: Larkspur Talent, Inc.
Website: www.larkspurtalent.example
Logos for Careerloop, Blipster, and Myriada

Name, Title, Office Number, Cell Number, email

Font styles to use
Serif
Sans Serif

Colors
0455a3
d5d5d5

Requirements
Nice to have
• The grey I selected below is not necessary - but, would like silver included. I included a card design (File 3: LTI early trial example.jpg) that I had started on. It's very rough, and not quite what we're looking for, but what we did like is the logo, big, maybe a bit faded, off center, goes out of frame, etc. Still looking for other ideas - you are the pros! But, just an idea of a design element we liked.

```html
<!DOCTYPE html>
<html lang="en">
<head>
<meta charset="utf-8">
<title>Larkspur Talent — Business Card</title>
<link rel="stylesheet" href="https://fonts.googleapis.com/css2?family=Alegreya+Sans:wght@400;500&family=Open+Sans:ital,wght@0,400;1,700&display=swap">
<style>
  :root {
    --stage: #1c1c1c;
    --paper: #ffffff;
    --brand-blue: #0455a3;
    --brand-blue-light: #2a8ad6;
    --ink: #2b2b2b;
    --ink-soft: #555555;
    --rule: #c9c9c9;
    --slate: #575757;
    --silver: #d5d5d5;
    --white: #ffffff;
  }
  * { margin: 0; padding: 0; box-sizing: border-box; }
  html, body { width: 1200px; height: 907px; overflow: hidden; background: var(--stage); }
  .canvas { position: relative; width: 1200px; height: 907px; }

  .card { position: absolute; left: 300px; width: 601px; height: 343px; overflow: hidden; }
  .card--front { top: 98px; background: var(--paper); }
  .card--back { top: 475px; background: var(--slate); }

  /* Brand name: one colour, one weight, one line, plain circle beside it */
  .brand {
    position: absolute; display: flex; align-items: center; gap: 9px;
    font-family: "Alegreya Sans", sans-serif; font-weight: 500;
    font-size: 27px; line-height: 30px; white-space: nowrap;
  }
  .brand__dot { width: 20px; height: 20px; border-radius: 50%; flex: none; }
  .brand--front { right: 323px; top: 126px; color: var(--ink); }
  .brand--front .brand__dot { background: var(--brand-blue); }
  .brand--back { right: 35px; top: 236px; color: var(--white); }
  .brand--back .brand__dot { background: var(--silver); }

  .divider { position: absolute; left: 300px; top: 80px; width: 1px; height: 149px; background: var(--rule); }

  /* Front: person */
  .person { position: absolute; left: 332px; top: 76px; }
  .person__name { font-family: "Alegreya Sans", sans-serif; font-weight: 500; font-size: 27px; color: var(--brand-blue); line-height: 30px; }
  .person__title { font-family: "Alegreya Sans", sans-serif; font-size: 18px; color: var(--ink-soft); line-height: 22px; }

  .contacts { position: absolute; left: 332px; top: 156px; list-style: none; }
  .contacts li {
    display: flex; align-items: center; gap: 6px; height: 22.5px;
    font-family: "Open Sans", sans-serif; font-size: 15px; color: var(--ink-soft);
  }
  .contacts svg { width: 14px; height: 14px; fill: var(--brand-blue); flex: none; }

  /* Front: web band */
  .web-band { position: absolute; left: 0; top: 288px; width: 601px; height: 34px; background: var(--slate); }
  .web-band__blue {
    position: absolute; left: 0; top: 0; width: 503px; height: 34px;
    background: linear-gradient(90deg, var(--brand-blue) 0%, var(--brand-blue-light) 55%, var(--brand-blue) 100%);
  }
  .web-band__url {
    position: absolute; left: 110px; top: 0; line-height: 34px;
    font-family: "Open Sans", sans-serif; font-style: italic; font-weight: 700;
    font-size: 14px; letter-spacing: 2.4px; color: var(--white);
  }
  .web-band__dot { position: absolute; left: 464px; top: 5px; width: 24px; height: 24px; border-radius: 50%; background: var(--white); }

  /* Back */
  .faded-mark {
    position: absolute; left: -10px; top: 8px; width: 310px; height: 310px; border-radius: 50%;
    background: radial-gradient(circle at 50% 40%, rgba(255,255,255,0.16) 0%, rgba(255,255,255,0.08) 65%, rgba(255,255,255,0.03) 100%);
  }
  .social { position: absolute; right: 36px; top: 36px; display: flex; gap: 10px; list-style: none; }
  .social li { font-family: "Open Sans", sans-serif; font-size: 11px; color: var(--silver); }
</style>
</head>
<body>
<main class="canvas">

  <section class="card card--front" aria-label="Business card front">
    <div class="brand brand--front"><span class="brand__dot"></span>Larkspur Talent</div>

    <div class="divider"></div>

    <div class="person">
      <div class="person__name">Dana Whitfield</div>
      <div class="person__title">Manager</div>
    </div>

    <ul class="contacts">
      <li>
        <svg viewBox="0 0 16 16" aria-hidden="true"><path d="M3.5 1.5l2.5 2.8-1.4 1.9c.9 2 2.6 3.9 4.9 5.2l1.9-1.3 2.8 2.5-1.6 2C7.6 14.1 1.9 8.4 1.4 3.1z"/></svg>
        713-555-0142
      </li>
      <li>
        <svg viewBox="0 0 16 16" aria-hidden="true"><path d="M4.5 1h7a1 1 0 0 1 1 1v12a1 1 0 0 1-1 1h-7a1 1 0 0 1-1-1V2a1 1 0 0 1 1-1zm1 2v5h5V3zm.5 6.5v1h1v-1zm2 0v1h1v-1zm2 0v1h1v-1zm-4 2v1h1v-1zm2 0v1h1v-1zm2 0v1h1v-1z"/></svg>
        348-555-0187
      </li>
      <li>
        <svg viewBox="0 0 16 16" aria-hidden="true"><path d="M1 3.5h14v9H1zm1.2 1L8 9l5.8-4.5z"/></svg>
        info@larkspurtalent.example
      </li>
    </ul>

    <div class="web-band">
      <div class="web-band__blue"></div>
      <div class="web-band__url">www.larkspurtalent.example</div>
      <div class="web-band__dot"></div>
    </div>
  </section>

  <section class="card card--back" aria-label="Business card back">
    <div class="faded-mark" role="img" aria-label="Large faded brand emblem, off center and bleeding off the card edge"></div>

    <ul class="social">
      <li>Careerloop</li>
      <li>Blipster</li>
      <li>Myriada</li>
    </ul>

    <div class="brand brand--back"><span class="brand__dot"></span>Larkspur Talent</div>
  </section>

</main>
</body>
</html>
```